Brightfield Ventures Inc. Letterhead

Creation of attractive and eye catching letterhead for a business start-up for the construction industry. Letterhead must relate to construction, but avoid standard hammer and tools in the design.

I forgot to add some details, sorry about that. Some pertinent info: Ph: 916-555-0187 brightfieldventures.example 448 Willowmere Ave, Ste 210 Folsom, CA 95999 info@brightfieldventures.example not sure if slogan should be in there" “Connecting construction professionals to create a purpose driven industry.” must be able to be used in word. Thanks!

```html
<!DOCTYPE html>
<html lang="en">
<head>
<meta charset="utf-8">
<title>Brightfield Ventures Inc. Letterhead</title>
<link href="https://fonts.googleapis.com/css2?family=Montserrat:wght@600&family=Source+Sans+3:wght@400&family=Open+Sans:wght@400;600&family=Arimo:wght@700&display=swap" rel="stylesheet">
<style>
  :root {
    --navy: #14235c;
    --red: #c0121b;
    --ink: #555555;
    --ink-soft: #4a4a4a;
    --paper: #ffffff;
    --backdrop: #e8e8e8;
    --rule: #3a4a86;
  }
  * { margin: 0; padding: 0; box-sizing: border-box; }
  html, body {
    width: 1200px;
    height: 1200px;
    overflow: hidden;
    background: var(--backdrop);
  }
  .letterhead {
    position: absolute;
    left: 196px;
    top: 30px;
    width: 808px;
    height: 1140px;
    background: var(--paper);
    overflow: hidden;
  }
  .brand {
    position: absolute;
    left: 61px;
    top: 62px;
    display: flex;
    align-items: center;
    gap: 12px;
  }
  .brand-mark {
    width: 44px;
    height: 44px;
    background: var(--red);
  }
  .brand-name {
    font-family: "Montserrat", sans-serif;
    font-weight: 600;
    font-size: 20px;
    line-height: 24px;
    letter-spacing: 1.5px;
    color: var(--navy);
    text-transform: uppercase;
  }
  .contact {
    position: absolute;
    left: 577px;
    top: 62px;
    font-family: "Open Sans", sans-serif;
    font-size: 11px;
    color: var(--ink-soft);
  }
  .contact-block {
    border-left: 1.5px solid var(--rule);
    padding-left: 5px;
    line-height: 17.5px;
  }
  .contact-block + .contact-block { margin-top: 6px; line-height: 15.5px; }
  .contact-line { display: flex; align-items: center; gap: 6px; }
  .contact-line svg { width: 10px; height: 10px; flex: none; }
  .letter {
    position: absolute;
    left: 61px;
    top: 241px;
    width: 685px;
  }
  .salutation {
    font-family: "Arimo", sans-serif;
    font-weight: 700;
    font-size: 17.5px;
    color: var(--ink);
    margin-bottom: 18px;
  }
  .letter p {
    font-family: "Source Sans 3", sans-serif;
    font-size: 16.4px;
    line-height: 21.2px;
    color: var(--ink);
    text-align: justify;
    text-align-last: left;
    margin-bottom: 21px;
  }
  .signature {
    position: absolute;
    left: 61px;
    top: 757px;
    width: 152px;
    height: 72px;
    background: linear-gradient(90deg, #f1f1f1, #f7f7f7);
  }
  .footer-band {
    position: absolute;
    left: 0;
    top: 1080px;
    width: 808px;
    height: 60px;
  }
  .footer-url {
    position: absolute;
    left: 0;
    width: 808px;
    top: 1109px;
    text-align: center;
    font-family: "Open Sans", sans-serif;
    font-size: 14px;
    letter-spacing: 2.2px;
    color: #ffffff;
  }
</style>
</head>
<body>
  <main class="letterhead">
    <header>
      <div class="brand">
        <span class="brand-mark"></span>
        <span class="brand-name">Brightfield<br>Ventures Inc.</span>
      </div>
      <address class="contact">
        <div class="contact-block">
          Po. box 201, Street Name,<br>City Name, Zip Code - 00000
        </div>
        <div class="contact-block">
          <div class="contact-line">
            <svg viewBox="0 0 10 10"><path d="M2 0.8 L3.6 0.5 L4.3 2.8 L3.2 3.6 Q4 5.6 6 6.8 L6.9 5.8 L9.3 6.6 L9 8.3 Q8.4 9.5 6.8 9.2 Q1.8 7.6 0.8 2.6 Q0.9 1.3 2 0.8 Z" fill="#c0121b"/></svg>
            <span>1-254-555-0132</span>
          </div>
          <div class="contact-line">
            <svg viewBox="0 0 10 10"><rect x="0.5" y="2" width="9" height="6.5" fill="#c0121b"/><path d="M0.8 2.3 L5 5.6 L9.2 2.3" stroke="#fff" stroke-width="0.9" fill="none"/></svg>
            <span>info@companyname.com</span>
          </div>
        </div>
      </address>
    </header>

    <section class="letter">
      <h1 class="salutation">Dear Mr. John,</h1>
      <p>Lorem Ipsum is simply dummy text of the printing and typesetting industry. Lorem Ipsum has been the industry's standard dummy text ever since the 1500s, when an unknown printer took a galley of type and scrambled it to make a type specimen book. It has survived not only five centuries, but also the leap into electronic typesetting, remaining essentially unchanged.</p>
      <p>The standard chunk of Lorem Ipsum used since the 1500s is reproduced below for those interested. Sections 1.10.32 and 1.10.33 from "de Finibus Bonorum et Malorum" by Cicero are also reproduced in their exact original form, accompanied by English versions from the 1914 translation by H. Rackham</p>
      <p>Lorem Ipsum is simply dummy text of the printing and typesetting industry. Lorem Ipsum has been the industry's standard dummy text ever since the 1500s, when an unknown printer took a galley of type and scrambled it to make a type specimen book. It has survived not only five centuries, but also the leap into electronic typesetting, remaining essentially unchanged. It was popularised in the</p>
      <p>Lorem Ipsum is simply dummy text of the printing and typesetting industry. Lorem Ipsum has been the industry's standard dummy text ever since the 1500s, when an unknown printer took a galley of type and scrambled it to make a type specimen book. It has survived not only five centuries, but also the leap into electronic typesetting, remaining essentially unchanged. It was popularised in the</p>
    </section>

    <div class="signature" role="img" aria-label="Handwritten signature of the sender"></div>

    <svg class="footer-band" viewBox="0 0 808 60" preserveAspectRatio="none" aria-hidden="true">
      <path d="M50 44 Q404 -38 756 44 Q404 -26 50 44 Z" fill="#14235c"/>
      <path d="M0 60 Q404 -28 808 60 Z" fill="#c0121b"/>
    </svg>
    <footer class="footer-url">www.companyname.com</footer>
  </main>
</body>
</html>
```